business card - Helicopter Flight Services, Flight School, etc.

We need a business card design for a new helicopter service.

We offer Helicopter Flight Services, Aerial Filming & Photography, Flight School, and Helicopter Tours. In that order.

Summit BladeAir, Inc.
Dennis Tollerby
SummitBladeair@Kestmail.com
626-418-7352

Based at the Brenwick Airport in Van Nuys, CA. The final design should communicate integrity and safety. Pictures or logos at your discretion.

Card back side - surprise me.

```html
<!DOCTYPE html>
<html lang="en">
<head>
<meta charset="utf-8">
<title>Summit BladeAir, Inc. — Business Card</title>
<link rel="stylesheet" href="https://fonts.googleapis.com/css2?family=Open+Sans:wght@400;600;700&display=swap">
<style>
  :root {
    --page-bg: #ecebe8;
    --card-white: #ffffff;
    --brand-blue: #1a6fc4;
    --brand-blue-dark: #0b3f98;
    --brand-blue-light: #3aa3dd;
    --band-grey: #4a4a4c;
    --text-grey: #3a3a3a;
    --card-shadow: rgba(0, 0, 0, 0.18);
  }
  * { margin: 0; padding: 0; box-sizing: border-box; }
  html, body {
    width: 1200px;
    height: 913px;
    overflow: hidden;
    background: var(--page-bg);
    font-family: "Open Sans", Arial, sans-serif;
  }
  .stage {
    position: relative;
    width: 1200px;
    height: 913px;
  }
  .card {
    position: absolute;
    width: 540px;
    height: 309px;
    border-radius: 4px;
    overflow: hidden;
    box-shadow: 0 10px 28px var(--card-shadow);
  }

  /* ---------- Front ---------- */
  .card-front {
    left: 70px;
    top: 150px;
    background: var(--card-white);
  }
  .front-brand {
    position: absolute;
    left: 70px;
    top: 72px;
    display: flex;
    align-items: center;
    gap: 12px;
  }
  .brand-dot {
    width: 22px;
    height: 22px;
    border-radius: 50%;
    background: var(--brand-blue);
  }
  .brand-name {
    font-weight: 700;
    font-size: 26px;
    letter-spacing: 0.5px;
    color: var(--brand-blue);
  }
  .divider-line {
    position: absolute;
    left: 0;
    top: 204px;
    width: 540px;
    height: 1.5px;
    background: var(--brand-blue);
  }
  .person-name {
    position: absolute;
    left: 30px;
    top: 156px;
    font-size: 22px;
    font-weight: 700;
    color: var(--brand-blue);
  }
  .person-title {
    position: absolute;
    left: 48px;
    top: 184px;
    font-size: 13px;
    color: var(--text-grey);
  }
  .contact-list {
    position: absolute;
    left: 76px;
    top: 220px;
    list-style: none;
  }
  .contact-item {
    display: flex;
    align-items: center;
    gap: 8px;
    font-size: 14px;
    line-height: 24px;
    color: var(--brand-blue);
  }
  .contact-icon { width: 13px; height: 13px; }
  .corner-band {
    position: absolute;
    left: 330px;
    top: 205px;
    width: 210px;
    height: 104px;
    background: linear-gradient(180deg, var(--brand-blue) 0%, var(--brand-blue-dark) 100%);
  }
  .base-band {
    position: absolute;
    left: 0;
    bottom: 0;
    width: 330px;
    height: 20px;
    background: var(--band-grey);
  }

  /* ---------- Back ---------- */
  .card-back {
    left: 590px;
    top: 450px;
    background: linear-gradient(160deg, var(--brand-blue-light) 0%, var(--brand-blue) 50%, var(--brand-blue-dark) 100%);
    color: var(--card-white);
  }
  .back-brand {
    position: absolute;
    left: 110px;
    top: 96px;
    display: flex;
    align-items: center;
    gap: 12px;
  }
  .back-brand .brand-dot { background: var(--card-white); }
  .back-brand .brand-name { color: var(--card-white); font-size: 28px; }
  .service-list {
    position: absolute;
    left: 170px;
    top: 160px;
    width: 300px;
    list-style: none;
    text-align: center;
    font-size: 15px;
    line-height: 24px;
  }
</style>
</head>
<body>
<main class="stage">

  <section class="card card-front" aria-label="Business card front">
    <div class="front-brand">
      <span class="brand-dot"></span>
      <span class="brand-name">Summit BladeAir, Inc.</span>
    </div>

    <h1 class="person-name">Dennis Tollerby</h1>
    <p class="person-title">Owner</p>
    <div class="divider-line"></div>

    <ul class="contact-list">
      <li class="contact-item">
        <svg class="contact-icon" viewBox="0 0 16 16" aria-hidden="true">
          <path d="M3.5 1.5l2.5 0 1 3.5-1.6 1.2a8 8 0 0 0 4.4 4.4L11 9l3.5 1v2.5c0 .8-.7 1.5-1.5 1.5A11.5 11.5 0 0 1 2 3c0-.8.7-1.5 1.5-1.5z" fill="var(--text-grey)"/>
        </svg>
        626-418-7352
      </li>
      <li class="contact-item">
        <svg class="contact-icon" viewBox="0 0 16 16" aria-hidden="true">
          <rect x="1.5" y="3.5" width="13" height="9" fill="none" stroke="var(--text-grey)" stroke-width="1.5"/>
          <path d="M1.5 3.5l6.5 5 6.5-5" fill="none" stroke="var(--text-grey)" stroke-width="1.5"/>
        </svg>
        SummitBladeair@Kestmail.com
      </li>
    </ul>

    <div class="corner-band"></div>
    <div class="base-band"></div>
  </section>

  <section class="card card-back" aria-label="Business card back">
    <div class="back-brand">
      <span class="brand-dot"></span>
      <span class="brand-name">Summit BladeAir, Inc.</span>
    </div>
    <ul class="service-list">
      <li>Aerial Filming &amp; Photography</li>
      <li>Flight School</li>
      <li>Helicopter Tours (in that order)</li>
    </ul>
  </section>

</main>
</body>
</html>
```